Detail Shop Business card design

i need a business card design for my new detailing company called 'Brisk's Polish Works'. i want an all black and white design . simple, direct and to the point. i want the designer to choose a fitting font to match the logothe front should have logo, address, phone and email and the back side should have a slogan and text indicating that we offer services on anything including cars, trucks, motorcycles and RVs. slogan will read "we take pride in your ride"
maybe also very small on the back side the IG icon with Brisks_Polish_Works

phone 208.417.6352
address 3847 E Larkin Ave
Spokane WA 99214
email: BrisksPolish@mailvexo.com

Target Market(s)

all ages , auto enthusiasts

Industry/Entity Type

Automotive

Contact Information for Business Card

the front should have logo, address, phone and email and the back side should have a slogan and text indicating that we offer services on anything including cars, trucks, motorcycles and RVs. slogan will read "we take pride in your ride"

phone 208.417.6352
address 3847 E Larkin Ave
Spokane WA 99214

Colors
000000
ffffff

Requirements
Must have
• bold font and very simple design with good spacing
Nice to have
• anything creative from the designer indicating we service any types of vehicles
Should not have
• any colors ,

```html
<!DOCTYPE html>
<html lang="en">
<head>
<meta charset="utf-8">
<title>Brisk's Polish Works – Business Card</title>
<link rel="stylesheet" href="https://fonts.googleapis.com/css2?family=Roboto:wght@400;500;700&family=Oswald:wght@500&display=swap">
<style>
  :root {
    --ink: #000000;
    --ink-soft: #333333;
    --paper: #ffffff;
    --backdrop: #9a9a9a;
    --art-tone: #6f6f6f;
  }
  * { box-sizing: border-box; margin: 0; padding: 0; }
  html, body { width: 1200px; height: 960px; overflow: hidden; }
  body { background: var(--backdrop); position: relative; font-family: "Roboto", sans-serif; color: var(--ink); }

  .card { position: absolute; width: 598px; height: 343px; background: var(--paper); overflow: hidden; box-shadow: 0 2px 4px rgba(0,0,0,.25); }
  .card--front { left: 322px; top: 110px; }
  .card--back { left: 320px; top: 493px; width: 600px; }

  /* Front */
  .brand { position: absolute; left: 380px; top: 70px; width: 200px; display: flex; align-items: center; gap: 8px; justify-content: center; }
  .brand__dot { width: 14px; height: 14px; border-radius: 50%; background: var(--ink); flex: none; }
  .brand__name { font-family: "Roboto", sans-serif; font-weight: 700; font-size: 19px; line-height: 1.2; color: var(--ink); }

  .person { position: absolute; left: 35px; top: 169px; }
  .person__name { font-weight: 500; font-size: 20px; letter-spacing: .2px; line-height: 1; }
  .person__role { font-size: 14px; color: var(--ink-soft); margin-top: 7px; letter-spacing: .3px; }

  .divider { position: absolute; left: 35px; top: 222px; width: 529px; height: 2px; background: var(--ink); }

  .contacts { position: absolute; left: 35px; top: 236px; list-style: none; }
  .contacts li { display: flex; align-items: center; gap: 8px; height: 19.3px; font-size: 14px; color: var(--ink-soft); }
  .contacts svg { width: 13px; height: 13px; fill: var(--ink); flex: none; }

  .address { position: absolute; right: 34px; top: 275px; text-align: right; font-size: 14px; line-height: 19px; color: var(--ink-soft); }

  .base-band { position: absolute; left: 0; bottom: 0; width: 100%; height: 17px; background: var(--ink); border-top: 3px solid #d9d9d9; }

  /* Back */
  .services { position: absolute; top: 46px; left: 0; width: 100%; text-align: center; font-family: "Oswald", sans-serif; font-weight: 500; font-size: 18px; letter-spacing: -.2px; color: var(--ink); }
  .vehicle-art { position: absolute; left: 18px; top: 112px; width: 554px; height: 190px; background: linear-gradient(180deg, var(--art-tone), #2a2a2a); border-radius: 40px 40px 20px 20px; }
  .ground { position: absolute; left: 0; bottom: 0; width: 100%; height: 80px; }
  .slogan { position: absolute; left: 0; bottom: 18px; width: 100%; text-align: center; font-weight: 700; font-size: 16px; color: var(--paper); letter-spacing: .3px; }
</style>
</head>
<body>

<section class="card card--front" aria-label="Business card front">
  <div class="brand">
    <span class="brand__dot"></span>
    <span class="brand__name">Brisk's Polish Works</span>
  </div>

  <div class="person">
    <p class="person__name">DALE HARTLEY</p>
    <p class="person__role">CEO/FOUNDER</p>
  </div>

  <div class="divider"></div>

  <ul class="contacts">
    <li>
      <svg viewBox="0 0 24 24" aria-hidden="true"><path d="M6.6 10.8a15.1 15.1 0 0 0 6.6 6.6l2.2-2.2c.3-.3.7-.4 1-.2 1.1.4 2.3.6 3.6.6.6 0 1 .4 1 1V20c0 .6-.4 1-1 1A17 17 0 0 1 3 4c0-.6.4-1 1-1h3.5c.6 0 1 .4 1 1 0 1.3.2 2.5.6 3.6.1.3 0 .7-.2 1z"/></svg>
      208.417.6352
    </li>
    <li>
      <svg viewBox="0 0 24 24" aria-hidden="true"><path d="M7 1h10a2 2 0 0 1 2 2v18a2 2 0 0 1-2 2H7a2 2 0 0 1-2-2V3a2 2 0 0 1 2-2zm0 3v14h10V4zm5 15.5a1 1 0 1 0 0 2 1 1 0 0 0 0-2z"/></svg>
      741 295 3086
    </li>
    <li>
      <svg viewBox="0 0 24 24" aria-hidden="true"><path d="M2 5h20v14H2zm2 2v.5l8 5 8-5V7zm0 3v7h16v-7l-8 5z"/></svg>
      BrisksPolish@mailvexo.com
    </li>
    <li>
      <svg viewBox="0 0 24 24" aria-hidden="true"><path d="M12 2a10 10 0 1 0 0 20 10 10 0 0 0 0-20zm-1 17.9A8 8 0 0 1 4.2 10L9 14.8v1a2 2 0 0 0 2 2zm6.9-2.5A2 2 0 0 0 16 16h-1v-3a1 1 0 0 0-1-1H8v-2h2a1 1 0 0 0 1-1V7h2a2 2 0 0 0 2-2v-.4a8 8 0 0 1 2.9 12.8z"/></svg>
      www.briskspolish.com
    </li>
  </ul>

  <address class="address" style="font-style:normal">
    3847 E Larkin Ave<br>
    Spokane WA 99214
  </address>

  <div class="base-band"></div>
</section>

<section class="card card--back" aria-label="Business card back">
  <p class="services">we offer services on anything including cars, trucks, motorcycles &amp; RVs</p>

  <div class="vehicle-art" role="img" aria-label="Black and white illustration of a classic hot rod car in side view"></div>

  <svg class="ground" viewBox="0 0 600 80" preserveAspectRatio="none" aria-hidden="true">
    <path d="M0 68 C 120 10, 480 10, 600 68 L600 80 L0 80 Z" fill="#000000"/>
  </svg>
  <p class="slogan">WE TAKE PRIDE IN YOUR RIDE</p>
</section>

</body>
</html>
```